Velmarotix - world unique technology for better life - please let them know who am i at first sight

We need a new business card for company which is a provider of unique crystal based technology suitable for all living being. For more information and final design you can use our brochure (our colours are black and blue from brochure).
We use Verdana font

Industry/Entity Type

Business

Contact Information for Business Card

regular dimension

Font styles to use
Other font styles liked:
• Verdana

Requirements
Must have
• Logo
• name
• function/position
• phone
• mobile
• e-mail
• adress
Nice to have
• inovative design (technology directed)

```html
<!DOCTYPE html>
<html lang="en">
<head>
<meta charset="utf-8">
<title>Velmarotix business card</title>
<link href="https://fonts.googleapis.com/css2?family=Open+Sans:wght@300;400&display=swap" rel="stylesheet">
<style>
  :root {
    --bg: #e9ebee;
    --card-white: #fbfbfc;
    --brand-blue: #22b4e0;
    --brand-blue-deep: #1596c8;
    --brand-blue-light: #3fcbea;
    --ink: #1d2a33;
    --muted: #6b6e72;
    --white: #ffffff;
  }
  * { box-sizing: border-box; margin: 0; padding: 0; }
  html, body { width: 1200px; height: 858px; overflow: hidden; }
  body {
    background: var(--bg);
    font-family: "Open Sans", Verdana, sans-serif;
    display: flex;
    align-items: center;
    justify-content: center;
    gap: 40px;
  }
  .card {
    position: relative;
    width: 540px;
    height: 309px;
    border-radius: 4px;
    overflow: hidden;
    box-shadow: 0 6px 18px rgba(0,0,0,0.15);
  }
  .card-front { background: var(--card-white); }
  .contact-panel { position: absolute; inset: 0; }

  .brand {
    position: absolute;
    display: flex;
    align-items: center;
    gap: 12px;
  }
  .brand-dot { border-radius: 50%; flex: none; }
  .brand-name {
    font-weight: 300;
    text-transform: uppercase;
    letter-spacing: 0.06em;
    white-space: nowrap;
  }
  .card-front .brand { left: 30px; top: 42px; }
  .card-front .brand-dot { width: 40px; height: 40px; background: var(--brand-blue); }
  .card-front .brand-name { font-size: 28px; color: var(--brand-blue); }

  .person { position: absolute; left: 30px; bottom: 40px; }
  .person-name { font-size: 19px; color: var(--brand-blue); font-weight: 400; }
  .person-role { font-size: 12px; color: var(--muted); margin-top: 2px; }

  .contact {
    position: absolute;
    right: 22px;
    top: 38px;
    list-style: none;
    color: var(--ink);
    font-size: 12.5px;
    line-height: 1.55;
    text-align: right;
  }
  .contact li { display: flex; justify-content: flex-end; align-items: flex-start; gap: 10px; }
  .contact .icon { width: 13px; height: 13px; flex: none; margin-top: 3px; }
  .contact .icon path, .contact .icon rect { fill: none; stroke: var(--white); stroke-width: 1.4; }

  .card-back {
    background: linear-gradient(160deg, var(--brand-blue-light) 0%, var(--brand-blue) 55%, var(--brand-blue-deep) 100%);
    display: flex;
    align-items: center;
    justify-content: center;
  }
  .card-back .brand { position: static; gap: 16px; }
  .card-back .brand-dot { width: 56px; height: 56px; background: var(--white); opacity: 0.9; }
  .card-back .brand-name { font-size: 40px; color: var(--white); }
</style>
</head>
<body>

  <section class="card card-front" aria-label="Business card, front">
    <svg class="contact-panel" viewBox="0 0 540 309" preserveAspectRatio="none" aria-hidden="true">
      <polygon points="350,0 540,0 540,309 290,309" fill="var(--brand-blue)"/>
    </svg>

    <div class="brand">
      <span class="brand-dot"></span>
      <span class="brand-name">Velmarotix</span>
    </div>

    <div class="person">
      <p class="person-name">Employee Name</p>
      <p class="person-role">Managing Director</p>
    </div>

    <ul class="contact">
      <li><span>+ xxx(x) xx xxx xxx</span>
        <svg class="icon" viewBox="0 0 13 13"><rect x="4" y="1" width="5" height="11" rx="1"/></svg></li>
      <li><span>+385(0) 51 420 973</span>
        <svg class="icon" viewBox="0 0 13 13"><path d="M2,4 C2,2 11,2 11,4 L10,6 H3 Z M3,6 V11 H10 V6"/></svg></li>
      <li><span>info@velmarotix.eu</span>
        <svg class="icon" viewBox="0 0 13 13"><rect x="1" y="3" width="11" height="7"/><path d="M1,3 L6.5,7 L12,3"/></svg></li>
      <li><span>28-34 Harlow Lane<br>London EC2R 7XN<br>United Kingdom</span>
        <svg class="icon" viewBox="0 0 13 13"><path d="M1,7 L6.5,2 L12,7 M3,6 V12 H10 V6"/></svg></li>
    </ul>
  </section>

  <section class="card card-back" aria-label="Business card, back">
    <div class="brand">
      <span class="brand-dot"></span>
      <span class="brand-name">Velmarotix</span>
    </div>
  </section>

</body>
</html>
```